GLOOMBAT BASH 2014 - Halloween Party

I need a 8.5x11 poster that can also be a jpeg for facebook and run as a display ad in print. I would like a facebook cover and profile picture that matches the poster. This is our 8th annual Halloween costume party and is our biggest event of the year.

Copy is as follows: (no particular order

8th Annual GLOOMBAT BASH
Halloween Costume Party
FRIDAY October 31st (need to emphasize date, usually I do it on Saturday.)
$400 in CASH PRIZES awarded at 9pm AND Midnight
DJ 7pm-2am in the tavern
Live music by VELVET PARROTS in the back room. 9pm.
Drink Specials, Munchies
$5 cover in advance, $10 at the door.
Briarfield Lodge, 4185 County Road 61, Hillsdale, NY

Target Market(s)

We are a bar and we have live music and a DJ for this party and are awarding for prizes for the best costumes (and other costumer categories.)

Industry/Entity Type

House

Font styles to use
Other font styles liked:
• halloween, spooky but readable

Requirements
Must have
• Must communicate the details clearly, be able to read from a distance. Due to the amount of Information we need to convey, I am willng to go 8x14 poster size. The emphasis should really be on "Gloombat Bash". "8th annual" is not very important and should be weighted less than Gloombat Bash.
Should not have
• shouldn't be too scary. I've had shop owners tell me that some are too scary to hang in their stores.

```html
<!DOCTYPE html>
<html lang="en">
<head>
<meta charset="utf-8">
<title>Gloombat Bash – Halloween Costume Party</title>
<link rel="stylesheet" href="https://fonts.googleapis.com/css2?family=Creepster&family=Rye&family=Josefin+Sans:wght@600&family=Special+Elite&display=swap">
<style>
  :root {
    --blood-pink: #ee5f6b;
    --night: #141b1e;
    --storm: #4a5557;
    --storm-light: #7c8584;
    --ground: #0c1012;
    --window-glow: #e79a2c;
    --ghost-white: #f3f1ee;
  }
  * { margin: 0; padding: 0; box-sizing: border-box; }
  html, body { width: 927px; height: 1200px; overflow: hidden; background: var(--night); }
  .poster {
    position: relative;
    width: 927px;
    height: 1200px;
    overflow: hidden;
    color: var(--blood-pink);
    text-align: center;
  }
  .sky {
    position: absolute; inset: 0;
    background:
      radial-gradient(ellipse 60% 30% at 30% 25%, var(--storm-light) 0%, transparent 70%),
      radial-gradient(ellipse 55% 25% at 75% 45%, var(--storm) 0%, transparent 70%),
      radial-gradient(ellipse 70% 30% at 45% 10%, var(--storm) 0%, transparent 75%),
      linear-gradient(180deg, #1f292c 0%, #2c3537 45%, #161d20 75%, var(--night) 100%);
  }
  .haunted-hill {
    position: absolute; left: 0; right: 0; bottom: 0; height: 370px;
    background:
      radial-gradient(ellipse 22% 40% at 58% 55%, #5b4a2c 0%, transparent 80%),
      linear-gradient(180deg, rgba(12,16,18,0) 0%, #1b1d1a 30%, var(--ground) 100%);
  }
  .abs { position: absolute; }
  .edition {
    left: 188px; top: 70px; width: 140px; text-align: left;
    font-family: "Creepster", cursive; font-size: 34px; line-height: 32px; letter-spacing: 1px;
  }
  .event-title {
    left: 0; right: 0; top: 128px;
    font-family: "Creepster", cursive; font-weight: 400;
    line-height: 0.88;
  }
  .event-title .line-one { display: block; font-size: 150px; letter-spacing: 6px; }
  .event-title .line-two { display: block; font-size: 158px; letter-spacing: 10px; }
  .party-kind {
    left: 0; right: 0; top: 423px;
    font-family: "Josefin Sans", sans-serif; font-size: 22px; letter-spacing: 2px;
    color: var(--ghost-white);
  }
  .party-kind .dot { display: inline-block; width: 13px; height: 13px; border-radius: 50%; background: var(--ghost-white); margin: 0 8px; vertical-align: 1px; }
  .event-date {
    left: 230px; top: 462px; text-align: left; white-space: nowrap;
    font-family: "Creepster", cursive;
  }
  .event-date .day { font-size: 100px; }
  .event-date .month { font-size: 40px; margin-left: 6px; }
  .event-date .num { font-size: 74px; }
  .details { left: 0; right: 0; top: 560px; font-family: "Rye", serif; line-height: 1; }
  .prize-amount { font-size: 86px; }
  .prize-label { font-size: 40px; margin-top: 2px; }
  .prize-times { font-size: 22px; margin-top: 6px; }
  .offers { font-size: 28px; margin-top: 16px; }
  .offers-big { font-size: 40px; }
  .cover { font-size: 20px; margin-top: 4px; line-height: 1.15; }
  .bubble { position: absolute; overflow: visible; }
  .bubble-text {
    position: absolute; color: var(--night); font-family: "Creepster", cursive; line-height: 0.95;
  }
  .dj-text { left: 58px; top: 733px; width: 170px; font-size: 30px; }
  .dj-text .big { font-size: 48px; }
  .band-text { left: 690px; top: 655px; width: 170px; font-size: 34px; }
  .band-text .name { font-family: "Special Elite", monospace; font-size: 23px; line-height: 1.05; display: block; margin: 4px 0; }
  .band-text .live { font-family: "Rye", serif; font-size: 20px; }
  .venue {
    left: 0; right: 0; top: 1128px;
    font-family: "Rye", serif; font-size: 23px; line-height: 1.15; letter-spacing: 1px;
  }
</style>
</head>
<body>
<main class="poster">
  <div class="sky" role="img" aria-label="Stormy night sky with grey clouds"></div>
  <div class="haunted-hill" role="img" aria-label="Illustration of a lit old house on a hill with bare trees, bats and an owl"></div>

  <p class="abs edition">8TH<br>ANNUAL</p>
  <h1 class="abs event-title"><span class="line-one">GLOOMBAT</span><span class="line-two">BASH</span></h1>
  <p class="abs party-kind"><span class="dot"></span>HALLOWEEN COSTUME PARTY<span class="dot"></span></p>
  <p class="abs event-date"><span class="day">FRIDAY</span><span class="month">OCT.</span><span class="num">31ST</span></p>

  <section class="abs details">
    <p class="prize-amount">$400</p>
    <p class="prize-label">CASH PRIZES</p>
    <p class="prize-times">AT 9PM AND MIDNIGHT</p>
    <p class="offers">DRINK SPECIALS,</p>
    <p class="offers-big">MUNCHIES</p>
    <p class="cover">$5 COVER IN ADVANCE<br>$10 AT THE DOOR</p>
  </section>

  <svg class="bubble" style="left:0;top:0" width="927" height="1200" aria-hidden="true">
    <g fill="var(--blood-pink)">
      <path d="M60 745 C40 700 130 695 150 712 C190 695 250 720 240 760 C255 800 215 835 170 828 C130 845 60 830 55 795 C35 780 45 755 60 745 Z"/>
      <path d="M680 670 C675 630 760 625 790 640 C840 628 880 660 870 700 C885 740 850 790 790 785 C740 800 680 780 680 745 C660 720 665 690 680 670 Z"/>
    </g>
    <g fill="none" stroke="var(--blood-pink)" stroke-width="4" stroke-linecap="round">
      <path d="M185 828 C175 860 215 860 205 885 C198 905 230 905 228 915"/>
      <path d="M740 788 C730 820 690 830 710 860 C725 885 690 905 700 940"/>
    </g>
  </svg>

  <p class="bubble-text dj-text">7PM-2AM<br><span class="big">DJ</span> IN THE TAVERN</p>
  <p class="bubble-text band-text">9PM<span class="name">VELVET PARROTS</span><span class="live">LIVE</span></p>

  <address class="abs venue" style="font-style:normal">BRIARFIELD LODGE, 4185<br>COUNTY ROAD 61, HILLSDALE, NY</address>
</main>
</body>
</html>
```